Dental specialist needs a sharp looking letterhead

I am looking for a letterhead to be used to send letters and communication between myself (a dental specialist) and other dentists.
My office is a state of the art dental specialty office.
I need to letterhead to also state:
Bertram L. Oswick DDS
2748 Tollard Avenue, Suite K
West Tollard, NY 14391
(716)392-5061
fax: (716)392-5087
oswickroot.com (**this email address may change)

i included my logo designs.
thank you

Target Market(s)

dentists

Industry/Entity Type

Communication

Requirements
Must have
• the included logo, whether the vertical or horizontal versions

```html
<!DOCTYPE html>
<html lang="en">
<head>
<meta charset="utf-8">
<title>Tollard Root Care P.C. Letterhead</title>
<link rel="stylesheet" href="https://fonts.googleapis.com/css2?family=Arimo:wght@400&display=swap">
<style>
  :root {
    --paper: #ffffff;
    --ink: #2b2b2b;
    --ink-dark: #111111;
    --brand-blue: #41a1da;
    --swoosh-black: #0b0b0b;
    --footer-text: #ffffff;
  }
  * { margin: 0; padding: 0; box-sizing: border-box; }
  html, body { width: 931px; height: 1200px; overflow: hidden; background: var(--paper); }
  .letterhead {
    position: relative;
    width: 931px;
    height: 1200px;
    background: var(--paper);
    font-family: "Arimo", Arial, sans-serif;
    color: var(--ink);
  }
  .brand {
    position: absolute;
    left: 41px;
    top: 120px;
    display: flex;
    align-items: center;
    gap: 8px;
  }
  .brand-dot {
    width: 14px;
    height: 14px;
    border-radius: 50%;
    background: var(--brand-blue);
  }
  .brand-name {
    font-size: 18px;
    font-weight: 400;
    letter-spacing: 0.5px;
    color: var(--ink-dark);
    white-space: nowrap;
  }
  .sender {
    position: absolute;
    right: 39px;
    top: 94px;
    text-align: right;
  }
  .sender-name { font-size: 20px; line-height: 26px; }
  .sender-line {
    font-size: 15px;
    line-height: 23px;
    display: flex;
    justify-content: flex-end;
    align-items: center;
    gap: 5px;
  }
  .sender-line svg { fill: var(--brand-blue); }
  .footer-wave {
    position: absolute;
    left: 0;
    top: 1070px;
    width: 931px;
    height: 130px;
  }
  .footer-contact {
    position: absolute;
    top: 1131px;
    left: 60px;
    display: flex;
    color: var(--footer-text);
    font-size: 16px;
    line-height: 21px;
  }
  .footer-item { display: flex; align-items: flex-start; gap: 5px; }
  .footer-item svg { fill: var(--footer-text); margin-top: 3px; flex: none; }
  .footer-fax { width: 159px; }
</style>
</head>
<body>
  <main class="letterhead">
    <header>
      <div class="brand">
        <span class="brand-dot"></span>
        <span class="brand-name">TOLLARD ROOT CARE P.C.</span>
      </div>
      <address class="sender" style="font-style:normal">
        <div class="sender-name">Bertram L. Oswick, DDS</div>
        <div class="sender-line">
          <svg width="14" height="14" viewBox="0 0 24 24" aria-hidden="true"><path d="M6.6 10.8a15.1 15.1 0 0 0 6.6 6.6l2.2-2.2a1 1 0 0 1 1-.25 11.4 11.4 0 0 0 3.6.57 1 1 0 0 1 1 1V20a1 1 0 0 1-1 1A17 17 0 0 1 3 4a1 1 0 0 1 1-1h3.5a1 1 0 0 1 1 1c0 1.25.2 2.45.57 3.6a1 1 0 0 1-.25 1z"/></svg>
          <span>716-392-5061</span>
        </div>
        <div class="sender-line">
          <svg width="15" height="11" viewBox="0 0 24 18" aria-hidden="true"><path d="M0 0h24v18H0z M2 2l10 7 10-7" fill="var(--brand-blue)"/><path d="M1 1l11 8 11-8" fill="none" stroke="#fff" stroke-width="1.6"/></svg>
          <span>oswickroot@postmail.com</span>
        </div>
      </address>
    </header>

    <footer>
      <svg class="footer-wave" viewBox="0 0 931 130" aria-hidden="true">
        <path d="M0 46 C250 16, 650 10, 931 79 L931 99 C650 32, 250 30, 0 49 Z" fill="var(--swoosh-black)"/>
        <path d="M0 53 C250 34, 650 36, 931 105 L931 130 L0 130 Z" fill="var(--brand-blue)"/>
      </svg>
      <div class="footer-contact">
        <div class="footer-item footer-fax">
          <svg width="16" height="14" viewBox="0 0 24 20" aria-hidden="true"><path d="M6 0h12v6H6z M2 7h20a2 2 0 0 1 2 2v7h-4v4H4v-4H0V9a2 2 0 0 1 2-2z M6 13v5h12v-5z"/></svg>
          <span>716-392-5087</span>
        </div>
        <div class="footer-item">
          <svg width="13" height="18" viewBox="0 0 24 34" aria-hidden="true"><path d="M12 0a12 12 0 0 1 12 12c0 9-12 22-12 22S0 21 0 12A12 12 0 0 1 12 0zm0 7a5 5 0 1 0 0 10 5 5 0 0 0 0-10z"/></svg>
          <span>2748 Tollard Avenue, Suite K<br>West Tollard, NY 14391</span>
        </div>
      </div>
    </footer>
  </main>
</body>
</html>
```